Bar Reverie VIP Card design

Looking for a design for a VIP card forguests wishing to purchase to avoid cover charges, skipping the line and othe advantages.

We used our logo on last years card.I've also attached a few of our previous cards. Looking for something fresh.

We are not apposed to a vertical card either way would be fine We will have to incorporate the kell brew logo on the card as well.

Industry/Entity Type

Bar Restaurant www.bar-q-example.com

Font styles to use
Decorative

```html
<!DOCTYPE html>
<html lang="en">
<head>
<meta charset="utf-8">
<title>Bar Reverie VIP Card</title>
<link rel="stylesheet" href="https://fonts.googleapis.com/css2?family=Cinzel:wght@400;700&family=Great+Vibes&family=Tinos&display=swap">
<style>
  :root {
    --page: #ebebed;
    --navy: #1d2235;
    --navy-light: #2a3049;
    --gold: #c9a836;
    --gold-light: #efd98a;
    --gold-deep: #a58e22;
    --ink-dark: #1a1a1a;
    --white: #ffffff;
  }
  * { box-sizing: border-box; margin: 0; padding: 0; }
  html, body {
    width: 848px; height: 1200px; overflow: hidden;
    background: var(--page);
  }
  .vip-card {
    position: absolute; left: 44px; top: 347px;
    width: 760px; height: 506px;
    background: radial-gradient(ellipse at 50% 45%, var(--navy-light) 0%, var(--navy) 70%);
    box-shadow: 14px 18px 22px rgba(0,0,0,0.45);
    overflow: hidden;
  }
  .frame-line {
    position: absolute; top: 0; width: 1.5px; height: 443px;
    background: var(--gold);
  }
  .frame-line--left { left: 19px; }
  .frame-line--right { right: 18px; }
  .side-flourish {
    position: absolute; top: 119px; width: 30px; height: 272px;
    background: linear-gradient(180deg, rgba(201,168,54,0) 0%, rgba(201,168,54,0.55) 30%, rgba(201,168,54,0.55) 70%, rgba(201,168,54,0) 100%);
  }
  .side-flourish--left { left: 3px; }
  .side-flourish--right { right: 3px; }
  .established {
    position: absolute; left: 53px; top: 27px;
    font-family: "Tinos", serif; font-size: 16px; color: var(--white);
  }
  .vip-emblem {
    position: absolute; left: 50%; top: 44px; transform: translateX(-50%);
    width: 130px; height: 128px; text-align: center;
  }
  .vip-emblem__wreath {
    position: absolute; inset: 0; border-radius: 50%;
    background: radial-gradient(circle, rgba(201,168,54,0) 52%, rgba(201,168,54,0.55) 62%, rgba(201,168,54,0) 74%);
  }
  .vip-emblem__year {
    position: relative; padding-top: 30px;
    font-family: "Cinzel", serif; font-size: 18px; letter-spacing: 3px; color: var(--white);
    line-height: 1.1;
  }
  .vip-emblem__label {
    position: relative; line-height: 1;
    font-family: "Cinzel", serif; font-weight: 700; font-size: 48px;
    background: linear-gradient(180deg, var(--gold-light), var(--gold));
    -webkit-background-clip: text; background-clip: text; color: transparent;
  }
  .bar-name {
    position: absolute; left: 0; right: 0; top: 200px; text-align: center;
    font-family: "Great Vibes", cursive; font-weight: 400; font-size: 112px; line-height: 1;
    color: var(--white);
  }
  .tagline {
    position: absolute; left: 181px; top: 336px; width: 383px; height: 34px;
    border-radius: 12px;
    background: linear-gradient(90deg, var(--gold), var(--gold-light) 50%, var(--gold));
    display: flex; align-items: center; justify-content: center;
    font-family: "Cinzel", serif; font-weight: 700; font-size: 16px; letter-spacing: 2px; color: var(--ink-dark);
  }
  .info-band {
    position: absolute; left: 19px; right: 18px; top: 443px; height: 63px;
    background: var(--gold-deep);
    font-family: "Tinos", serif; color: var(--white);
  }
  .partner {
    position: absolute; left: 30px; top: 50%; transform: translateY(-50%);
    display: flex; align-items: center; gap: 6px;
    font-family: "Tinos", serif; font-size: 15px; color: var(--white);
  }
  .partner__mark { width: 12px; height: 12px; background: var(--white); }
  .location {
    position: absolute; left: 242px; top: 50%; transform: translateY(-50%);
    display: flex; align-items: center; gap: 7px;
    font-size: 14px;
  }
  .website {
    position: absolute; left: 529px; top: 50%; transform: translateY(-50%);
    font-size: 14px; letter-spacing: 0.6px;
  }
</style>
</head>
<body>
  <div class="vip-card">
    <div class="frame-line frame-line--left"></div>
    <div class="frame-line frame-line--right"></div>

    <div class="side-flourish side-flourish--left" role="img" aria-label="Gold wavy side ornament"></div>
    <div class="side-flourish side-flourish--right" role="img" aria-label="Gold wavy side ornament"></div>

    <p class="established">ESTD - 1981</p>

    <div class="vip-emblem">
      <div class="vip-emblem__wreath" role="img" aria-label="Gold laurel wreath with stars framing the VIP mark"></div>
      <p class="vip-emblem__year">2023</p>
      <p class="vip-emblem__label">VIP</p>
    </div>

    <h1 class="bar-name">Bar Reverie</h1>

    <p class="tagline">WHERE SUMMER NEVER ENDS</p>

    <div class="info-band">
      <div class="partner"><span class="partner__mark"></span>KELL BREW</div>
      <div class="location">
        <svg width="12" height="16" viewBox="0 0 12 16" aria-hidden="true">
          <path d="M6 0 C2.7 0 0 2.6 0 5.8 C0 10 6 16 6 16 C6 16 12 10 12 5.8 C12 2.6 9.3 0 6 0 Z M6 8.2 A2.4 2.4 0 1 1 6 3.4 A2.4 2.4 0 1 1 6 8.2 Z" fill="#ffffff"/>
        </svg>
        LAKE MAREN NEW JERSEY
      </div>
      <div class="website">www.bar-q-example.com</div>
    </div>
  </div>
</body>
</html>
```